Website Banner Design Needed for Health/Medical Business

We are looking for a creative and professional set of banners for the front page of our:
1. website - kelvoramedics.com.au and lunetaskin.com.au and bluemoorcare.com.au

then edit the above banners to the corrrect sizes for below
2. Our facebook pages (1 for each of the above websites)

3. Our google + pages (2 in total one for melb and syd)

4. You tube pages (1 for kelvoramedics and 1 for lunetaskin)

We are looking for something fresh and clean that gives the feeling of:
1. Medical (dont show pictures of doctors though - nurses are ok - just not doctors)
2. Modern because PRP is a modern medical procedure
3. Most Experienced - No other clinic in Australia has performed as many PRP treatments compared to us.
4. We offer a 100% money back guarantee as well

The banners will not be animated or using layers. they will be still banners.

We would prefer to use new stock images and will purchase them for you after you have provided some suggestions/initial drafts.

Target Market(s)

men and women from 25-65

Industry/Entity Type

Health And Wellness

Number of Pages Required

1 page

Font styles to use
Sans Serif

Requirements
Must have
• no doctor images
• nurses are ok - but no doctor images
• for the images avoid fake themed images eg. a person looking in the mirror at their hair loss = NO NO NO..... instead aim for a nurse holding a test tube or a clipboard .
• The banners need to emphasise we are the only clinic who has performed 11,000+ treatments in australia
Nice to have
• a medical feeling would be nice - but dont make it too medical. i want the viewer to associate the word TRUSTED PROVEN and RELIABLE when they view the banner.
Should not have
• as mentioned no doctor or images that look like hospital too much.
• we are a private clinic run by nurses - i have to becareful not to mislead the viewer

```html
<!DOCTYPE html>
<html lang="en">
<head>
<meta charset="utf-8">
<title>Hair Loss PRP Clinic Banner</title>
<link rel="stylesheet" href="https://fonts.googleapis.com/css2?family=League+Gothic&family=Montserrat:wght@400;700&family=Great+Vibes&display=swap">
<style>
  :root {
    --photo-warm: #8b6a56;
    --photo-light: #d8c4ae;
    --photo-mid: #a58b73;
    --photo-dark: #6b5648;
    --photo-teal: #3fb3c4;
    --ribbon-blue: #2d88c9;
    --ribbon-navy: #1d4f8a;
    --ribbon-green-soft: #c9e8aa;
    --ribbon-green: #8cc63f;
    --badge-blue: #1e5690;
    --paper: #ffffff;
    --ink-grey: #4a4a4a;
    --headline: #ffffff;
  }
  * { margin: 0; padding: 0; box-sizing: border-box; }
  html, body {
    width: 1200px;
    height: 626px;
    overflow: hidden;
    background: var(--paper);
  }
  .banner {
    position: relative;
    width: 1200px;
    height: 626px;
    overflow: hidden;
  }
  .banner__photo {
    position: absolute;
    inset: 0;
    background:
      radial-gradient(ellipse 140px 90px at 920px 470px, var(--photo-teal) 0%, rgba(63,179,196,0) 100%),
      linear-gradient(90deg, var(--photo-warm) 0%, var(--photo-mid) 30%, var(--photo-light) 52%, var(--photo-mid) 72%, var(--photo-dark) 100%);
  }
  .banner__waves {
    position: absolute;
    inset: 0;
    width: 1200px;
    height: 626px;
  }
  .headline {
    position: absolute;
    left: 43px;
    top: 84px;
    color: var(--headline);
    font-family: "League Gothic", "Arial Narrow", sans-serif;
    font-weight: 400;
    text-transform: uppercase;
    line-height: 1;
  }
  .headline__main {
    display: block;
    font-size: 76px;
    letter-spacing: -0.5px;
  }
  .headline__sub {
    display: block;
    font-size: 57px;
    margin-top: 4px;
  }
  .claim {
    position: absolute;
    left: 45px;
    top: 510px;
    color: var(--ink-grey);
    font-family: "Montserrat", Arial, sans-serif;
    line-height: 1.25;
  }
  .claim__lead {
    display: block;
    font-size: 20px;
    font-weight: 400;
  }
  .claim__figure {
    display: block;
    font-size: 27px;
    font-weight: 700;
  }
  .badge-text {
    font-family: "Montserrat", Arial, sans-serif;
    fill: var(--paper);
    text-anchor: middle;
  }
  .badge-tagline {
    font-family: "Great Vibes", cursive;
    font-size: 30px;
    fill: var(--paper);
  }
</style>
</head>
<body>
  <div class="banner">
    <div class="banner__photo" role="img" aria-label="Photo of two smiling nurses in pink and teal scrubs outside a clinic"></div>

    <svg class="banner__waves" viewBox="0 0 1200 626" aria-hidden="true">
      <path class="wave-base" fill="var(--paper)"
        d="M0,282 C120,272 250,285 380,322 C460,345 560,375 640,405 C790,462 920,528 1200,475 L1200,626 L0,626 Z"/>
      <path class="wave-green-soft-left" fill="var(--ribbon-green-soft)"
        d="M0,292 C150,278 300,302 450,345 C300,320 150,314 0,332 Z"/>
      <path class="wave-green-soft-center" fill="var(--ribbon-green-soft)"
        d="M250,372 C450,380 600,440 760,500 C850,532 930,555 1000,560 L1000,578 C900,580 820,556 720,522 C560,464 420,402 250,372 Z"/>
      <path class="wave-green-soft-right" fill="var(--ribbon-green-soft)"
        d="M1062,470 C1120,430 1170,372 1200,322 L1200,362 C1170,412 1122,456 1074,484 Z"/>
      <path class="wave-blue" fill="var(--ribbon-blue)"
        d="M0,332 C220,300 450,335 640,405 C790,462 920,528 1200,475 L1200,512 C920,566 790,500 640,443 C450,372 220,370 0,404 Z"/>
      <path class="wave-line-navy" fill="none" stroke="var(--ribbon-navy)" stroke-width="2.5"
        d="M0,487 C80,430 160,405 240,410 C450,425 700,560 884,592"/>
      <path class="wave-line-green" fill="none" stroke="var(--ribbon-green)" stroke-width="2.5"
        d="M0,434 C80,410 130,398 200,400 C400,410 600,560 931,598"/>
      <path class="wave-line-green-right" fill="none" stroke="var(--ribbon-green)" stroke-width="2.5"
        d="M1084,500 C1130,470 1170,440 1200,413"/>

      <g class="guarantee-badge">
        <circle cx="1002" cy="506" r="80" fill="var(--paper)"/>
        <circle cx="1002" cy="506" r="72" fill="var(--badge-blue)"/>
        <text class="badge-text" x="1002" y="500" font-size="34" font-weight="700">100%</text>
        <text class="badge-text" x="1002" y="528" font-size="16" font-weight="400">Money Back</text>
        <text class="badge-text" x="1002" y="550" font-size="17" font-weight="700">Guarantee</text>
        <path id="badge-arc" fill="none" d="M898,513 A104,104 0 0 1 1085,443"/>
        <text class="badge-tagline"><textPath href="#badge-arc">Reliable &amp; Trusted</textPath></text>
      </g>
    </svg>

    <h1 class="headline">
      <span class="headline__main">Loosing your hair</span>
      <span class="headline__sub">is a choice</span>
    </h1>

    <p class="claim">
      <span class="claim__lead">Only Australian clinic to perform</span>
      <span class="claim__figure">11,000+ PRP treatments</span>
    </p>
  </div>
</body>
</html>
```